Modern Homepage Design for brenvik.nl – Fish & Chicken Food Webshop

Brenvik.nl is an online store that sells fish and chicken food. The design should be visually appealing, easy to navigate, and optimized for e-commerce. We want a layout that helps customers quickly find what they need and encourages them to explore our products.
A good example of the style and structure we like is dierkamp.nl – clean layout, clear product focus, and user-friendly navigation.
Brand Colors (must be used):
Orange: #f7a441
Dark Gray: #3c3c3b
White: #ffffff
Please use these colors consistently throughout the design.
Homepage Requirements:
The homepage should include the following sections:
Main Slider / Hero Banner
A large, eye-catching slider at the top of the page to highlight promotions or featured categories.
Category Blocks
A section with clear, clickable blocks or tiles that link to main product categories (e.g., Fish Food, Chicken Food, Accessories).
Featured Products
A section showcasing selected or best-selling products.
Special Offers / Promotions
A space to highlight current deals or limited-time offers.
Three Banners in a Row
A section with three horizontal banners side by side, which can be used for promotions, shipping info, or other key messages.
Unique Selling Points (USPs)
A section that briefly explains what makes our store different (e.g., fast delivery, high-quality feed, trusted by professionals).
SEO Content Block
A short paragraph of text for SEO purposes (use Lorem Ipsum for dummy content).
Footer Design
Include space for contact information, navigation links, and social media.
Design Notes:
The design must be responsive and mobile-friendly.
Focus on clean layout, good spacing, and easy navigation.
Use modern fonts and a clear visual hierarchy.
We are only looking for the homepage design at this stage, but we may work with the selected designer on additional pages later.
Deliverables:
Homepage design in layered PSD, Figma, or Adobe XD format
Any fonts and assets used
Preview images/mockups
We look forward to seeing your ideas and working with a designer who can bring our brand to life with a fresh and functional homepage design.
Let us know if you have any questions.
Hobby Animal Keepers, Pet Owners
Animal Nutrition & Feed
2 page

```html
<!DOCTYPE html>
<html lang="en">
<head>
<meta charset="utf-8">
<title>Brenvik – Fish & Poultry Feed</title>
<link href="https://fonts.googleapis.com/css2?family=Poppins:wght@600;700;800&family=Roboto:wght@400;500;700&display=swap" rel="stylesheet">
<style>
:root{
  --orange:#f7a441;
  --dark:#3c3c3b;
  --ink:#2b2b2b;
  --white:#ffffff;
  --grey-bg:#f1f1f1;
  --nav-bg:#f3f3f3;
  --footer:#383838;
}
*{box-sizing:border-box;margin:0;padding:0}
html,body{width:1200px;height:4367px;overflow:hidden}
body{position:relative;background:var(--white);font-family:"Roboto",sans-serif;color:var(--ink)}
.abs{position:absolute}
h1,h2,h3,.display{font-family:"Poppins",sans-serif}
svg{display:block}

.topbar{left:0;top:0;width:1200px;height:48px;background:var(--orange);color:#fff;font-size:14px;font-weight:500}
.topbar .ship{position:absolute;left:110px;top:16px}
.topbar .links{position:absolute;right:0;top:0;height:48px;display:flex}
.topbar .links span{display:flex;align-items:center;gap:8px;padding:0 26px;border-left:1px solid rgba(255,255,255,.45)}
.topbar .links span:first-child{border-left:none}

.brand{display:flex;align-items:center;gap:8px}
.brand .dot{width:70px;height:70px;border-radius:50%;background:var(--orange)}
.brand .name{font-family:"Poppins",sans-serif;font-weight:700;color:var(--dark);font-size:66px;line-height:1;letter-spacing:-1px}
.search{left:514px;top:82px;width:340px;height:40px;border-radius:20px;background:#f0f0f0;font-size:13px;color:#444;display:flex;align-items:center;gap:12px;padding-left:6px}
.icircle{width:30px;height:30px;border-radius:50%;background:var(--orange);display:flex;align-items:center;justify-content:center}
.icircle.light{background:#fde8cf}
.account{left:880px;top:88px;display:flex;align-items:center;gap:18px;font-size:15px}
.account .login{color:var(--orange);text-decoration:underline;font-weight:500}
.account .total{font-weight:700}

.nav{left:0;top:153px;width:1200px;height:49px;background:var(--nav-bg);border-top:1px solid #e6e6e6}
.nav ul{list-style:none;display:flex;gap:32px;position:absolute;left:126px;top:17px;font-size:13px;font-weight:700;text-transform:uppercase}
.nav li.active{color:var(--orange);text-decoration:underline}

.hero-main{left:112px;top:229px;width:581px;height:429px;border-radius:40px;overflow:hidden;background:linear-gradient(120deg,#0f2e38 0%,#1e4a55 40%,#5f5a45 70%,#b88440 100%)}
.hero-side{left:712px;top:229px;width:376px;height:429px;border-radius:40px;overflow:hidden;background:linear-gradient(180deg,#dba23c 0%,#d39428 60%,#bf7d1e 100%)}
.hero-title{color:#fff;font-weight:800;text-transform:uppercase;line-height:1.13}
.btn{display:inline-flex;align-items:center;gap:8px;border-radius:24px;font-weight:700;font-size:14px;text-transform:uppercase}
.btn.solid{background:var(--orange);color:#fff}
.btn.white{background:#fff;color:var(--ink)}
.btn.outline{border:2px solid var(--orange);color:var(--ink);background:#fff}
.arrow-btn{width:34px;height:34px;border-radius:50%;display:flex;align-items:center;justify-content:center}
.arrow-btn.on{background:var(--orange)}
.arrow-btn.off{background:#e4e4e4}
.dots{left:346px;top:686px;display:flex;gap:12px}
.dots i{width:13px;height:13px;border-radius:50%;border:1.5px solid #999;display:block}
.dots i.on{background:var(--orange);border-color:var(--orange)}
.rule{left:0;top:734px;width:1200px;height:1px;background:#e3e3e3}

.sec-title{font-size:42px;font-weight:800;text-align:center;width:1200px;left:0}
.sec-title::after{content:"";display:block;width:72px;height:3px;background:var(--orange);margin:6px auto 0}

.cat{width:180px;text-align:center}
.cat .ring{width:178px;height:178px;border-radius:50%;background:#fbeee3;margin:0 auto;position:relative;overflow:hidden}
.cat .ring .fill{position:absolute;left:30%;top:18%;width:40%;height:66%;border-radius:45%}
.cat.active .ring{border:3px solid var(--orange);background:#fff}
.cat.active .ring .bg{position:absolute;inset:6px;border-radius:50%;background:#f7ece2}
.cat .label{margin-top:20px;font-size:17px;font-weight:700;text-transform:uppercase;display:flex;justify-content:center;gap:8px}
.cat.active .label{color:var(--orange)}
.cat.active .label b{text-decoration:underline}

.featured-bg{left:0;top:1231px;width:1200px;height:547px;background:var(--grey-bg)}
.card{width:222px;height:310px;background:#fff;border-radius:14px;box-shadow:0 3px 10px rgba(0,0,0,.08);padding:0 17px}
.card .img{height:120px;margin:16px 0 18px;display:flex;align-items:center;justify-content:center}
.card .img div{width:150px;height:58px;border-radius:50% 50% 40% 40%}
.card .price{color:var(--orange);font-size:14px;font-weight:500}
.card h3{font-family:"Roboto",sans-serif;font-size:15px;font-weight:700;text-transform:uppercase;margin:8px 0 6px}
.card p{font-size:12px;line-height:1.6;color:#444}
.card .btn{margin-top:12px;height:38px;padding:0 20px;font-size:12px}
.card .heart{position:absolute;right:14px;top:12px}

.promo{left:112px;top:1885px;width:976px;height:469px;border-radius:50px;background:#e6e6e6;overflow:hidden}
.promo .glow{position:absolute;left:560px;top:38px;width:390px;height:390px;border-radius:50%;background:#fbe3c4}
.promo .photo{position:absolute;left:540px;top:70px;width:400px;height:399px;border-radius:180px 180px 0 0;background:linear-gradient(90deg,#e8c48a 0%,#d9a560 45%,#eb8e38 60%,#f09a45 100%)}

.usp{width:302px;height:327px;border-radius:22px;background:#fff;border-left:3px solid var(--orange);box-shadow:0 4px 14px rgba(0,0,0,.1);text-align:center;padding-top:30px}
.usp .ic{width:90px;height:90px;border-radius:50%;background:var(--orange);margin:0 auto 28px;display:flex;align-items:center;justify-content:center}
.usp h3{font-family:"Roboto",sans-serif;font-size:15px;font-weight:700;text-transform:uppercase;margin-bottom:12px}
.usp p{font-size:14px;line-height:1.55;color:#444;padding:0 24px}

.banner{width:376px;height:343px;border-radius:22px;overflow:hidden;color:#fff;padding:60px 0 0 34px}
.banner h3{font-size:31px;font-weight:800;line-height:1.2;text-transform:uppercase}
.banner h3::after{content:"";display:block;width:56px;height:3px;background:var(--orange);margin-top:2px}
.banner p{font-size:17px;line-height:1.55;margin-top:12px}
.banner .btn{margin-top:22px;height:44px;padding:0 26px}

.about-photo{left:112px;top:3402px;width:446px;height:446px;border-radius:50%;background:linear-gradient(160deg,#3d9bb6 0%,#1c6a86 45%,#0f3b52 100%)}
.about h2{font-size:42px;font-weight:800}
.about h2::after{content:"";display:block;width:72px;height:3px;background:var(--orange);margin-top:4px}
.about p{font-size:16px;line-height:1.55;color:#444;text-align:justify;margin-top:18px}

.footer{left:0;top:3956px;width:1200px;height:411px;background:var(--footer);color:#fff}
.footer h4{font-family:"Roboto",sans-serif;font-size:17px;font-weight:700;text-transform:uppercase}
.footer ul{list-style:none;margin-top:20px}
.footer li{font-size:13px;margin-bottom:17px;display:flex;align-items:center;gap:16px}
.footer li::before{content:"";width:5px;height:5px;border-radius:50%;background:var(--orange)}
.contact-row{display:flex;align-items:center;gap:20px;font-size:14px;margin-bottom:20px}
.contact-row .cc{width:36px;height:36px;border-radius:50%;background:#fff;display:flex;align-items:center;justify-content:center;flex:none}
.social{display:flex;gap:8px}
.social i{width:30px;height:30px;border-radius:50%;background:#fff;display:block}
.social i.on{background:var(--orange)}
.pay{display:flex;gap:6px}
.pay i{width:34px;height:20px;border-radius:3px;display:block;background:#e6e6e6}
</style>
</head>
<body>

<div class="abs topbar">
  <div class="ship">FREE SHIPPING ON ORDERS OVER €50</div>
  <div class="links">
    <span><svg width="14" height="14" viewBox="0 0 24 24"><path fill="#fff" d="M6.6 10.8a15.2 15.2 0 006.6 6.6l2.2-2.2a1 1 0 011-.25 11.4 11.4 0 003.6.6 1 1 0 011 1V20a1 1 0 01-1 1A17 17 0 013 4a1 1 0 011-1h3.5a1 1 0 011 1c0 1.25.2 2.45.6 3.6a1 1 0 01-.25 1z"/></svg>CONTACT US</span>
    <span><svg width="15" height="14" viewBox="0 0 24 22"><path fill="#fff" d="M12 21l-1.5-1.3C5 15 2 12.2 2 8.5A5.4 5.4 0 017.5 3 6 6 0 0112 5a6 6 0 014.5-2A5.4 5.4 0 0122 8.5c0 3.7-3 6.5-8.5 11.2z"/></svg>WISHLIST</span>
    <span><svg width="16" height="14" viewBox="0 0 24 22"><path fill="#fff" d="M1 2h4l3 12h12l3-9H7"/><circle cx="9" cy="19" r="2" fill="#fff"/><circle cx="18" cy="19" r="2" fill="#fff"/></svg>ADD TO CART</span>
  </div>
</div>

<div class="abs brand" style="left:112px;top:64px"><div class="dot"></div><div class="name">brenvik</div></div>
<div class="abs search">
  <div class="icircle"><svg width="14" height="14" viewBox="0 0 24 24"><circle cx="10" cy="10" r="6" stroke="#fff" stroke-width="3" fill="none"/><path d="M15 15l6 6" stroke="#fff" stroke-width="3"/></svg></div>
  Search For
</div>
<div class="abs account">
  <span style="display:flex;align-items:center;gap:16px"><span class="icircle"><svg width="14" height="14" viewBox="0 0 24 24"><circle cx="12" cy="8" r="5" fill="#fff"/><path d="M3 22a9 9 0 0118 0z" fill="#fff"/></svg></span><span class="login">LOGIN</span></span>
  <span style="display:flex;align-items:center;gap:16px"><span class="icircle light"><svg width="14" height="13" viewBox="0 0 24 22"><path fill="none" stroke="#f7a441" stroke-width="3" d="M1 2h4l3 12h12l3-9H7"/><circle cx="9" cy="19" r="2" fill="#f7a441"/><circle cx="18" cy="19" r="2" fill="#f7a441"/></svg></span><span class="total">$0.00</span></span>
</div>

<nav class="abs nav">
  <ul><li class="active">Home</li><li>Product Categories ▾</li><li>Featured Products ▾</li><li>Accessories</li><li>Offers</li><li>Other Products</li><li>Garden Animals</li></ul>
</nav>

<div class="abs hero-main" role="img" aria-label="Goldfish swimming among feed pellets in dark blue water">
  <div class="abs" style="left:60px;top:60px">
    <h1 class="hero-title" style="font-size:44px">High-Quality<br>Feed for<br>Fish &amp; Poultry</h1>
    <p style="color:#fff;font-size:20px;line-height:1.45;margin-top:10px;width:420px">Trusted by professionals for nutrition and freshness.</p>
    <span class="btn solid" style="height:44px;padding:0 32px;margin-top:28px"><svg width="15" height="13" viewBox="0 0 24 22"><path fill="#fff" d="M1 2h4l3 12h12l3-9H7"/><circle cx="9" cy="19" r="2" fill="#fff"/><circle cx="18" cy="19" r="2" fill="#fff"/></svg>Shop Now</span>
  </div>
</div>
<div class="abs hero-side" role="img" aria-label="Terrier dog jumping over scattered dog food kibble">
  <div class="abs" style="left:38px;top:188px">
    <h1 class="hero-title" style="font-size:46px;line-height:1.22">Premium<br>Dog Food</h1>
    <span class="btn white" style="height:44px;padding:0 30px;margin-top:20px"><svg width="15" height="13" viewBox="0 0 24 22"><path fill="#2b2b2b" d="M1 2h4l3 12h12l3-9H7"/><circle cx="9" cy="19" r="2" fill="#2b2b2b"/><circle cx="18" cy="19" r="2" fill="#2b2b2b"/></svg>Shop Now</span>
  </div>
</div>
<div class="abs arrow-btn on" style="left:1129px;top:405px"><svg width="12" height="12" viewBox="0 0 12 12"><path d="M4 2l4 4-4 4" stroke="#fff" stroke-width="2" fill="none"/></svg></div>
<div class="abs arrow-btn off" style="left:1129px;top:446px"><svg width="12" height="12" viewBox="0 0 12 12"><path d="M8 2L4 6l4 4" stroke="#333" stroke-width="2" fill="none"/></svg></div>
<div class="abs dots"><i></i><i class="on"></i><i></i><i></i><i></i></div>
<div class="abs rule"></div>

<h2 class="abs sec-title" style="top:822px">PRODUCT CATEGORIES</h2>
<div class="abs arrow-btn off" style="left:1013px;top:851px"><svg width="12" height="12" viewBox="0 0 12 12"><path d="M8 2L4 6l4 4" stroke="#333" stroke-width="2" fill="none"/></svg></div>
<div class="abs arrow-btn on" style="left:1053px;top:851px"><svg width="12" height="12" viewBox="0 0 12 12"><path d="M4 2l4 4-4 4" stroke="#fff" stroke-width="2" fill="none"/></svg></div>

<div class="abs cat" style="left:110px;top:919px"><div class="ring" role="img" aria-label="Orange goldfish"><div class="fill" style="background:linear-gradient(180deg,#f59a3a,#f27a1c)"></div></div><div class="label"><b>Fish</b> <span>➞</span></div></div>
<div class="abs cat" style="left:310px;top:919px"><div class="ring" role="img" aria-label="White chicken"><div class="fill" style="background:linear-gradient(180deg,#ececec,#cfcfcf)"></div></div><div class="label"><b>Chicken</b> <span>➞</span></div></div>
<div class="abs cat active" style="left:510px;top:916px"><div class="ring" role="img" aria-label="Green parrot"><div class="bg"></div><div class="fill" style="background:linear-gradient(180deg,#6aa83a,#2f6e24)"></div></div><div class="label" style="margin-top:14px"><b>Bird</b> <span>➞</span></div></div>
<div class="abs cat" style="left:708px;top:919px"><div class="ring" role="img" aria-label="Happy brown dog"><div class="fill" style="background:linear-gradient(180deg,#b9773c,#8a4f22)"></div></div><div class="label"><b>Dog</b> <span>➞</span></div></div>
<div class="abs cat" style="left:908px;top:919px"><div class="ring" role="img" aria-label="Hamster"><div class="fill" style="background:linear-gradient(180deg,#d99a55,#b56a2e)"></div></div><div class="label"><b>Rodent</b> <span>➞</span></div></div>

<div class="abs featured-bg"></div>
<h2 class="abs sec-title" style="top:1296px">FEATURED PRODUCTS</h2>
<div class="abs arrow-btn off" style="left:1013px;top:1309px"><svg width="12" height="12" viewBox="0 0 12 12"><path d="M8 2L4 6l4 4" stroke="#333" stroke-width="2" fill="none"/></svg></div>
<div class="abs arrow-btn on" style="left:1053px;top:1309px"><svg width="12" height="12" viewBox="0 0 12 12"><path d="M4 2l4 4-4 4" stroke="#fff" stroke-width="2" fill="none"/></svg></div>

<div class="abs card" style="left:112px;top:1390px">
  <svg class="heart" width="16" height="15" viewBox="0 0 24 22"><path fill="none" stroke="#f7a441" stroke-width="2" d="M12 20l-1.5-1.3C5 14 2 11.2 2 7.5A5 5 0 017.5 2 6 6 0 0112 4a6 6 0 014.5-2A5 5 0 0122 7.5c0 3.7-3 6.5-8.5 11.2z"/></svg>
  <div class="img" role="img" aria-label="Pile of fish food flakes"><div style="background:linear-gradient(180deg,#c98a5c,#9c5530)"></div></div>
  <div class="price">€ 14.99</div><h3>Fish Food Flakes</h3>
  <p>Sed ut perspiciatis undeoaome nis iste natusea</p>
  <span class="btn outline"><svg width="13" height="12" viewBox="0 0 24 22"><path fill="#2b2b2b" d="M1 2h4l3 12h12l3-9H7"/><circle cx="9" cy="19" r="2"/><circle cx="18" cy="19" r="2"/></svg>Add to Cart</span>
</div>
<div class="abs card" style="left:363px;top:1390px">
  <svg class="heart" width="16" height="15" viewBox="0 0 24 22"><path fill="none" stroke="#f7a441" stroke-width="2" d="M12 20l-1.5-1.3C5 14 2 11.2 2 7.5A5 5 0 017.5 2 6 6 0 0112 4a6 6 0 014.5-2A5 5 0 0122 7.5c0 3.7-3 6.5-8.5 11.2z"/></svg>
  <div class="img" role="img" aria-label="Pile of chicken grain feed"><div style="background:linear-gradient(180deg,#d7bf92,#a9864f)"></div></div>
  <div class="price">€ 14.99</div><h3>Chicken Feed</h3>
  <p>Sed ut perspiciatis undeoaome nis iste natusea</p>
  <span class="btn outline"><svg width="13" height="12" viewBox="0 0 24 22"><path fill="#2b2b2b" d="M1 2h4l3 12h12l3-9H7"/><circle cx="9" cy="19" r="2"/><circle cx="18" cy="19" r="2"/></svg>Add to Cart</span>
</div>
<div class="abs card" style="left:614px;top:1390px">
  <svg class="heart" width="16" height="15" viewBox="0 0 24 22"><path fill="#f7a441" d="M12 20l-1.5-1.3C5 14 2 11.2 2 7.5A5 5 0 017.5 2 6 6 0 0112 4a6 6 0 014.5-2A5 5 0 0122 7.5c0 3.7-3 6.5-8.5 11.2z"/></svg>
  <div class="img" role="img" aria-label="Pile of red and green fish food pellets"><div style="background:linear-gradient(180deg,#7d7a3a,#8e3f25)"></div></div>
  <div class="price">€ 14.99</div><h3>Fish Food Pellets</h3>
  <p>Sed ut perspiciatis undeoaome nis iste natusea</p>
  <span class="btn solid" style="border:2px solid var(--orange)"><svg width="13" height="12" viewBox="0 0 24 22"><path fill="#fff" d="M1 2h4l3 12h12l3-9H7"/><circle cx="9" cy="19" r="2" fill="#fff"/><circle cx="18" cy="19" r="2" fill="#fff"/></svg>Add to Cart</span>
</div>
<div class="abs card" style="left:865px;top:1390px">
  <svg class="heart" width="16" height="15" viewBox="0 0 24 22"><path fill="none" stroke="#f7a441" stroke-width="2" d="M12 20l-1.5-1.3C5 14 2 11.2 2 7.5A5 5 0 017.5 2 6 6 0 0112 4a6 6 0 014.5-2A5 5 0 0122 7.5c0 3.7-3 6.5-8.5 11.2z"/></svg>
  <div class="img" role="img" aria-label="Open can of cat food"><div style="width:96px;height:96px;border-radius:14px;background:linear-gradient(180deg,#dcdcdc,#a9a9a9)"></div></div>
  <div class="price">€ 14.99</div><h3>Cat Food</h3>
  <p>Sed ut perspiciatis undeoaome nis iste natusea</p>
  <span class="btn outline"><svg width="13" height="12" viewBox="0 0 24 22"><path fill="#2b2b2b" d="M1 2h4l3 12h12l3-9H7"/><circle cx="9" cy="19" r="2"/><circle cx="18" cy="19" r="2"/></svg>Add to Cart</span>
</div>

<div class="abs promo">
  <div class="glow"></div>
  <div class="photo" role="img" aria-label="Golden retriever and orange cat sitting behind a bowl of food"></div>
  <div class="abs" style="left:58px;top:82px">
    <div class="display" style="font-size:54px;font-weight:800;line-height:1.1">SAVE UP TO 25%</div>
    <div class="display" style="font-size:45px;font-weight:600;line-height:1.15;border-bottom:3px solid var(--orange);display:inline-block">THIS SEASON!</div>
    <p style="font-size:21px;line-height:1.55;color:#333;margin-top:16px;width:470px">Exceptional quality, now at exclusive prices. Explore special offers curated for professionals and enthusiasts alike.</p>
    <span class="btn solid" style="height:44px;padding:0 30px;margin-top:24px"><svg width="15" height="13" viewBox="0 0 24 22"><path fill="#fff" d="M1 2h4l3 12h12l3-9H7"/><circle cx="9" cy="19" r="2" fill="#fff"/><circle cx="18" cy="19" r="2" fill="#fff"/></svg>Shop Offers</span>
  </div>
</div>

<h2 class="abs sec-title" style="top:2445px">WHY CHOOSE BRENVIK?</h2>
<div class="abs usp" style="left:112px;top:2539px">
  <div class="ic"><svg width="46" height="40" viewBox="0 0 46 40"><rect x="14" y="6" width="22" height="22" rx="3" fill="#fff"/><path d="M2 12h10M4 18h8M6 24h6" stroke="#fff" stroke-width="3"/><circle cx="36" cy="30" r="8" fill="#fff"/><path d="M32 30l3 3 5-6" stroke="#f7a441" stroke-width="2.5" fill="none"/></svg></div>
  <h3>Fast Delivery</h3>
  <p>Lorem ipsum dolor sit amet, consectetur adipiscing elit, sed do eiusmod tempor incididunt ut labore et dolore magna aliqua. Ut enim ad minim veniam, quis nostrud exercitationea.</p>
</div>
<div class="abs usp" style="left:449px;top:2539px">
  <div class="ic"><svg width="46" height="46" viewBox="0 0 46 46"><circle cx="23" cy="23" r="17" fill="none" stroke="#fff" stroke-width="4"/><path d="M15 23l6 6 11-12" stroke="#fff" stroke-width="4" fill="none"/></svg></div>
  <h3>High-Quality Feed</h3>
  <p>Lorem ipsum dolor sit amet, consectetur adipiscing elit, sed do eiusmod tempor incididunt ut labore et dolore magna aliqua. Ut enim ad minim veniam, quis nostrud exercitationea.</p>
</div>
<div class="abs usp" style="left:787px;top:2539px">
  <div class="ic"><svg width="50" height="40" viewBox="0 0 50 40"><path d="M3 20l10-10 10 6 10-6 14 10-12 12-8-6-6 6z" fill="#fff"/><circle cx="25" cy="8" r="6" fill="#fff"/></svg></div>
  <h3>Trusted by Professionals</h3>
  <p>Lorem ipsum dolor sit amet, consectetur adipiscing elit, sed do eiusmod tempor incididunt ut labore et dolore magna aliqua. Ut enim ad minim veniam, quis nostrud exercitationea.</p>
</div>

<div class="abs banner" style="left:17px;top:2966px;background:linear-gradient(90deg,#2e3034 0%,#3a3835 50%,#7d5f3d 80%,#b98d55 100%)" role="img" aria-label="Rooster pecking grain feed">
  <h3>Free Shipping<br>Over €50</h3>
  <p>Enjoy fast, reliable delivery<br>on all orders above €50.</p>
  <span class="btn white"><svg width="15" height="13" viewBox="0 0 24 22"><path fill="#2b2b2b" d="M1 2h4l3 12h12l3-9H7"/><circle cx="9" cy="19" r="2"/><circle cx="18" cy="19" r="2"/></svg>Shop Now</span>
</div>
<div class="abs banner" style="left:412px;top:2966px;background:linear-gradient(90deg,#2a2926 0%,#34312b 50%,#6e5d43 80%,#a48c68 100%)" role="img" aria-label="Poodle puppy eating from a food bowl">
  <h3>Same-Day<br>Dispatch</h3>
  <p>Place your order before 2 PM and<br>we’ll ship it the same day.</p>
  <span class="btn solid">Learn More <span>➞</span></span>
</div>
<div class="abs banner" style="left:805px;top:2966px;background:linear-gradient(90deg,#26331f 0%,#33462a 50%,#566a36 80%,#7a6e48 100%)" role="img" aria-label="Squirrel on a park bench with people playing in the background">
  <h3>Expert<br>Support</h3>
  <p>Questions about feed types or<br>care? Our team is here to help.</p>
  <span class="btn white"><svg width="13" height="13" viewBox="0 0 24 24"><path fill="#2b2b2b" d="M6.6 10.8a15.2 15.2 0 006.6 6.6l2.2-2.2a1 1 0 011-.25 11.4 11.4 0 003.6.6 1 1 0 011 1V20a1 1 0 01-1 1A17 17 0 013 4a1 1 0 011-1h3.5a1 1 0 011 1c0 1.25.2 2.45.6 3.6a1 1 0 01-.25 1z"/></svg>Contact Us</span>
</div>

<div class="abs about-photo" role="img" aria-label="Hand holding feed pellets underwater with a fish swimming toward it"></div>
<div class="abs about" style="left:678px;top:3447px;width:410px">
  <h2>ABOUT US</h2>
  <p>Lorem ipsum dolor sit amet, consectetur adipiscing elit, sed do eiusmod tempor incididunt ut labore et dolore magna aliqua. Ut enim ad minim veniam, quis nostrud exercitation ullamco laboris nisi ut aliquip ex ea comm tempor incididuntodo consequat.</p>
  <p>Lorem ipsum dolor sit amet, consectetur adipiscing elit, sed do eiusmod tempor incididunt ut labore et dolore magna aliqua.</p>
  <span class="btn solid" style="height:44px;padding:0 28px;margin-top:30px">Learn More <span>➞</span></span>
</div>

<footer class="abs footer">
  <div class="abs" style="left:112px;top:140px;display:flex;align-items:center;gap:8px">
    <div style="width:56px;height:56px;border-radius:50%;background:var(--orange)"></div>
    <div style="font-family:Poppins,sans-serif;font-weight:700;font-size:52px;line-height:1;color:#fff">brenvik</div>
  </div>
  <div class="abs social" style="left:158px;top:222px"><i class="on"></i><i></i><i></i><i></i></div>

  <div class="abs" style="left:378px;top:57px">
    <h4>Other Links</h4>
    <ul><li>Home</li><li>Product Categories</li><li>Featured Products</li><li>Accessories</li><li>Offers</li><li>Other Products</li><li>Garden animals</li></ul>
  </div>

  <div class="abs" style="left:556px;top:57px">
    <h4>Contact Us</h4>
    <div style="margin-top:20px">
      <div class="contact-row"><span class="cc"><svg width="14" height="16" viewBox="0 0 24 28"><path fill="#f7a441" d="M12 0a10 10 0 00-10 10c0 7 10 18 10 18s10-11 10-18A10 10 0 0012 0zm0 14a4 4 0 110-8 4 4 0 010 8z"/></svg></span><span style="line-height:1.4">465, Lorum Ipsum Dolore,<br>United States</span></div>
      <div class="contact-row"><span class="cc"><svg width="16" height="12" viewBox="0 0 24 18"><rect width="24" height="18" rx="2" fill="#f7a441"/><path d="M1 2l11 8 11-8" stroke="#fff" stroke-width="2" fill="none"/></svg></span>info@brenvik.nl</div>
      <div class="contact-row"><span class="cc"><svg width="14" height="14" viewBox="0 0 24 24"><path fill="#f7a441" d="M6.6 10.8a15.2 15.2 0 006.6 6.6l2.2-2.2a1 1 0 011-.25 11.4 11.4 0 003.6.6 1 1 0 011 1V20a1 1 0 01-1 1A17 17 0 013 4a1 1 0 011-1h3.5a1 1 0 011 1c0 1.25.2 2.45.6 3.6a1 1 0 01-.25 1z"/></svg></span>085-0123456</div>
      <div class="contact-row"><span class="cc"><svg width="14" height="14" viewBox="0 0 24 24"><path fill="#f7a441" d="M6.6 10.8a15.2 15.2 0 006.6 6.6l2.2-2.2a1 1 0 011-.25 11.4 11.4 0 003.6.6 1 1 0 011 1V20a1 1 0 01-1 1A17 17 0 013 4a1 1 0 011-1h3.5a1 1 0 011 1c0 1.25.2 2.45.6 3.6a1 1 0 01-.25 1z"/></svg></span>0612345678</div>
    </div>
  </div>

  <div class="abs" style="left:814px;top:57px;width:274px">
    <h4>Sign Up to Our Newsletter</h4>
    <div style="margin-top:24px;font-size:13px;padding-bottom:8px;border-bottom:1px solid #9a9a9a">Email</div>
    <span class="btn solid" style="height:46px;padding:0 26px;margin-top:12px"><svg width="16" height="14" viewBox="0 0 24 22"><path fill="#fff" d="M23 1L1 10l7 3 2 8 4-5 6 4z"/></svg>Subscribe</span>
  </div>

  <div class="abs" style="left:112px;top:346px;width:976px;height:1px;background:#5a5a5a"></div>
  <div class="abs" style="left:0;top:368px;width:1200px;text-align:center;font-size:13px">© 2025 BRENVIK &nbsp;|&nbsp; All Rights Reserved</div>
  <div class="abs pay" style="left:906px;top:366px"><i></i><i></i><i></i><i></i><i></i></div>
</footer>

</body>
</html>
```